UK Online Auction Site needs a clever design

We need a contemporary landing page and registration page design for a UK auction website, that look equally at home on PC's and tablets . The design should be fresh, bright, clean, professional, robust, and familiar. We would like to see something clever but functional.

Online

```html
<!DOCTYPE html>
<html lang="en">
<head>
<meta charset="utf-8">
<title>Bidwell – UK Online Auctions</title>
<link rel="stylesheet" href="https://fonts.googleapis.com/css2?family=Open+Sans:ital,wght@0,400;0,600;0,700;1,600&display=swap">
<style>
:root{
  --blue:#1a8fd9;
  --blue-dark:#0b74c4;
  --orange:#f39a1a;
  --orange-hot:#f47a1f;
  --text:#333;
  --muted:#8a8a8a;
  --line:#dedede;
  --bg:#ffffff;
  --topbar:#f0f0f0;
}
*{box-sizing:border-box;margin:0;padding:0}
html,body{width:745px;height:1200px;overflow:hidden;background:var(--bg);font-family:"Open Sans",Arial,sans-serif;color:var(--text)}
.page{position:relative;width:745px;height:1200px}
.topbar{position:absolute;left:0;top:0;width:745px;height:13px;background:var(--topbar);border-bottom:1px solid #e6e6e6}
.brand{position:absolute;left:48px;top:34px;display:flex;align-items:center;gap:8px;font-size:30px;font-weight:700;color:var(--blue)}
.brand-dot{width:14px;height:14px;border-radius:50%;background:var(--blue)}
.mainnav{position:absolute;left:350px;top:34px;height:50px;display:flex;border:1px solid var(--line);background:#fff}
.mainnav a{display:flex;flex-direction:column;align-items:center;justify-content:center;gap:3px;padding:0 10px;min-width:48px;border-left:1px solid var(--line);font-size:10px;color:#444;text-decoration:none;white-space:nowrap}
.mainnav a:first-child{border-left:0}
.mainnav svg{width:14px;height:14px;fill:#888}
.categories{position:absolute;left:48px;top:93px;width:157px}
.categories h2{height:35px;background:linear-gradient(#3aa7ea,var(--blue));color:#fff;font-size:13px;font-weight:400;padding:8px 15px;white-space:nowrap}
.categories ul{list-style:none;border:1px solid var(--line);border-top:0}
.categories li{height:21.6px;line-height:21px;font-size:9px;padding-left:28px;border-top:1px solid #ececec;position:relative;color:#444;white-space:nowrap}
.categories li::before{content:"";position:absolute;left:17px;top:8px;width:4px;height:4px;border-right:1px solid #999;border-top:1px solid #999;transform:rotate(45deg)}
.search{position:absolute;left:212px;top:96px;width:484px;height:30px;border:1px solid var(--line);display:flex;align-items:center;padding:0 8px 0 14px;gap:8px;font-size:11px;color:#555;white-space:nowrap}
.search .select{width:85px;height:20px;border:1px solid #ddd;font-size:8px;color:#777;padding:4px 10px;background:#f8f8f8}
.search .field{flex:1;height:20px;border:1px solid #ddd;font-size:8px;color:#999;padding:4px 10px}
.search .go{width:30px;height:20px;background:var(--orange-hot);display:flex;align-items:center;justify-content:center;margin-left:-9px}
.hero{position:absolute;left:212px;top:133px;width:484px;height:175px;border:1px solid var(--line);overflow:hidden}
.hero-copy{position:absolute;left:26px;top:32px;width:210px;z-index:1}
.hero-copy h1{font-size:21px;font-weight:400;color:var(--orange-hot);line-height:1.2;white-space:nowrap}
.hero-copy h2{font-size:14px;font-weight:400;color:var(--blue);margin-top:2px;white-space:nowrap}
.hero-copy p{font-size:7.5px;color:#999;line-height:1.6;margin-top:3px}
.btn{display:inline-block;background:var(--orange);color:#fff;font-weight:600;text-align:center;white-space:nowrap}
.hero-copy .btn{font-size:9px;padding:3px 0;width:76px;margin-top:8px}
.hero-photo{position:absolute;left:232px;top:0;width:252px;height:175px;background:radial-gradient(ellipse at 55% 45%,#d9343a 0 22%,#e9eef2 40%,#ffffff 75%)}
.arrows{position:absolute;display:flex;gap:4px}
.arrows svg{width:8px;height:12px;stroke:currentColor;fill:none;stroke-width:1.3}
.hero .arrows{right:10px;bottom:8px;color:#888}
.infobox{position:absolute;top:322px;height:163px;border:1px solid var(--line);padding:10px 14px}
.infobox h3{font-size:11.5px;font-weight:400;color:#333;margin:3px 0 5px;white-space:nowrap}
.infobox p{font-size:7.5px;color:#888;line-height:1.85}
.signin .btn{display:block;background:var(--blue-dark);font-size:11px;font-weight:400;padding:3px 0;margin-top:8px}
.signin small{display:block;font-size:6.5px;color:#555;margin-top:6px;white-space:nowrap}
.confidence{padding:10px 0}
.confidence h3{padding-left:14px}
.trust{display:flex;gap:10px;padding:4px 10px;border-top:1px solid #ececec;height:44px;align-items:flex-start}
.trust:first-of-type{border-top:0}
.trust svg{width:26px;height:26px;flex:none;margin-top:3px}
.trust b{display:block;font-size:9px;font-weight:400;color:var(--blue);white-space:nowrap}
.trust span{font-size:7px;color:#888;line-height:1.4;display:block}
.promo{position:absolute;left:533px;top:322px;width:164px;height:163px;background:linear-gradient(135deg,#1360c4,#1f8be2 60%,#1a62c0);overflow:hidden;color:#fff;font-style:italic;font-weight:600;font-size:14px;line-height:1.3;padding:6px 8px;white-space:nowrap}
.promo span{display:block}
.promo .r{text-align:right}
.promo-badge{position:absolute;right:-16px;bottom:2px;width:46px;height:46px;border-radius:50%;background:var(--orange)}
.section-head{position:absolute;left:48px;width:649px;height:31px;color:#fff;font-size:13px;padding:6px 15px}
.section-head .arrows{right:14px;top:10px;color:#fff}
.featured-head{top:500px;background:linear-gradient(#f7a531,var(--orange))}
.stores-head{top:744px;background:linear-gradient(#1e9be3,var(--blue-dark))}
.products{position:absolute;left:48px;width:649px;height:200px;border:1px solid var(--line);border-top:0;display:flex}
.product{flex:1;min-width:0;border-left:1px solid var(--line);padding:14px 10px 0 12px}
.product:first-child{border-left:0}
.product .photo{height:94px;margin:0 auto 12px;width:84px;border-radius:4px}
.product h4{font-size:9.5px;font-weight:600;color:#333;white-space:nowrap}
.product p{font-size:7.5px;color:#999;line-height:1.65;margin-top:1px}
.buy{display:flex;align-items:center;gap:6px;margin-top:5px;white-space:nowrap}
.buy strong{font-size:11.5px;font-weight:400;flex:none;white-space:nowrap}
.buy .btn{font-size:6.5px;padding:4px 0;width:57px;flex:none}
.g-dark{background:linear-gradient(#3a3a3a,#111)}
.g-silver{background:linear-gradient(#f3f3f3,#b9bcc0)}
.g-screen{background:linear-gradient(#d14aa8,#6c3aa8 55%,#c9ccd0 56%)}
.g-teal{background:linear-gradient(#1fb3cf,#1b1b1b)}
.footer{position:absolute;left:0;top:1010px;width:745px;height:154px;background:linear-gradient(#1aa3df,var(--blue-dark));color:#fff;display:flex;padding:28px 0 0 62px}
.footer section{width:116px}
.footer section:nth-child(3){width:127px}
.footer h5{font-size:11.5px;font-weight:400;margin-bottom:2px;white-space:nowrap}
.footer li{list-style:none;font-size:7.5px;font-weight:600;line-height:16px;white-space:nowrap}
.social{display:flex;gap:5px;margin-top:7px}
.social span{width:20px;height:20px;border-radius:50%;background:#fff;opacity:.92}
.bottombar{position:absolute;left:0;top:1164px;width:745px;height:36px;background:var(--blue-dark);font-size:7.5px;color:#9ccdf0;padding:14px 0 0 58px;white-space:nowrap}
</style>
</head>
<body>
<div class="page">
  <div class="topbar"></div>

  <div class="brand"><span class="brand-dot"></span>Bidwell</div>

  <nav class="mainnav">
    <a href="#"><svg viewBox="0 0 16 16"><text x="3" y="14" font-size="16" font-family="Arial">$</text></svg>Sell</a>
    <a href="#"><svg viewBox="0 0 16 16"><path d="M6 1h2v7h1V5h2v3h1V6h2v6l-2 4H7L3 10l1-1 2 2z"/></svg>Sign In</a>
    <a href="#"><svg viewBox="0 0 16 16"><path d="M2 3h12v2H2zM3 6h10l-1 9H4z"/></svg>Basket</a>
    <a href="#"><svg viewBox="0 0 16 16"><text x="3" y="14" font-size="16" font-family="Arial" font-weight="bold">?</text></svg>Help</a>
    <a href="#"><svg viewBox="0 0 16 16"><path d="M1 6q7-5 14 0l-2 2-2-1V6H5v1L3 8zM4 9h8l2 5H2z"/></svg>Contact</a>
    <a href="#"><svg viewBox="0 0 16 16"><circle cx="8" cy="5" r="4"/><path d="M1 16q0-6 7-6t7 6z"/></svg>Register</a>
  </nav>

  <aside class="categories">
    <h2>Shop by Category</h2>
    <ul>
      <li>Fashion</li><li>Home &amp; Garden</li><li>Electricals &amp; Technology</li><li>Collectables &amp; Antiques</li>
      <li>Jewellery &amp; Beauty</li><li>Toys</li><li>Sport &amp; Leisure</li><li>Motors</li>
    </ul>
  </aside>

  <div class="search">
    <span>Search here</span>
    <span class="select">All Categories ⌄</span>
    <span class="field">type your word</span>
    <span class="go"><svg width="12" height="12" viewBox="0 0 12 12" fill="none" stroke="#fff" stroke-width="1.6"><circle cx="5" cy="5" r="3.6"/><path d="M7.6 7.6L11 11"/></svg></span>
  </div>

  <section class="hero">
    <div class="hero-photo" role="img" aria-label="Red waterproof compact camera splashing in water"></div>
    <div class="hero-copy">
      <h1>Phasellus felis dolor</h1>
      <h2>Scelerisque tempus eget</h2>
      <p>Phasellus felis dolor scelerisque a tempus eget lobortis id libero Aliquam nec erat at purus cursus</p>
      <span class="btn">View All</span>
    </div>
    <div class="arrows"><svg viewBox="0 0 8 12"><path d="M7 1L2 6l5 5"/></svg><svg viewBox="0 0 8 12"><path d="M1 1l5 5-5 5"/></svg></div>
  </section>

  <section class="infobox" style="left:48px;width:161px">
    <h3 style="font-size:12px">Welcome</h3>
    <p>Phasellus felis dolor scelerisque a tempus eget lobortis id libero Aliquam nec erat at purus cursus interdum Vestibulum ligula augue bibendum accumsan vestibulum ut commodo a mi Morbi ornare gravida elit Integer congue augue et malesuada iaculis</p>
  </section>

  <section class="infobox signin" style="left:208px;width:162px">
    <h3>Sign In</h3>
    <p>Phasellus felis dolor scelerisque a tempus eget lobortis id libero Aliquam nec erat at purus cursus interdum Vestibulum ligula augue bibendum accumsan</p>
    <span class="btn">Sign In</span>
    <small>Don't have an account? Register ›</small>
  </section>

  <section class="infobox confidence" style="left:369px;width:162px">
    <h3>Shop with confidence</h3>
    <div class="trust">
      <svg viewBox="0 0 26 26"><path d="M13 2l9 3v7c0 6-4 10-9 12C8 22 4 18 4 12V5z" fill="#3a9a3a"/><path d="M8 13l4 4 7-8" stroke="#fff" stroke-width="2.2" fill="none"/></svg>
      <div><b>Completely safe</b><span>Aliquam nec erat at purus cursus interdum Vesti</span></div>
    </div>
    <div class="trust">
      <svg viewBox="0 0 26 26"><path d="M7 3h12v6a6 6 0 01-12 0z" fill="#e0a820"/><path d="M12 15h2v5h4v3H8v-3h4z" fill="#c8901a"/></svg>
      <div><b>Premium sellers</b><span>Aliquam nec erat at purus cursus interdum Vesti</span></div>
    </div>
    <div class="trust">
      <svg viewBox="0 0 26 26"><rect x="1" y="8" width="22" height="8" rx="2" fill="#1a8fd9"/><path d="M16 14v9l2-2 2 3 1-1-2-3h3z" fill="#333"/></svg>
      <div><b>Feedback rating system</b><span>Aliquam nec erat at purus cursus interdum Vesti</span></div>
    </div>
  </section>

  <aside class="promo">
    <span>Make Your Presence</span>
    <span class="r">On The NET</span>
    <span>GET A WEBSITE AT</span>
    <span class="r" style="padding-right:12px">$ 89 Only</span>
    <div class="promo-badge" role="img" aria-label="Christmas offer sticker"></div>
  </aside>

  <div class="section-head featured-head">Featured Product
    <div class="arrows"><svg viewBox="0 0 8 12"><path d="M7 1L2 6l5 5"/></svg><svg viewBox="0 0 8 12"><path d="M1 1l5 5-5 5"/></svg></div>
  </div>
  <div class="products" style="top:531px">
    <article class="product"><div class="photo g-dark" role="img" aria-label="Black portable hard drive on stand"></div><h4>Product Name</h4><p>Integer congue augue et malesuada iaculis</p><div class="buy"><strong>$&nbsp;2,100</strong><span class="btn">Add to Cart</span></div></article>
    <article class="product"><div class="photo g-silver" role="img" aria-label="Silver tower desktop computer"></div><h4>Product Name</h4><p>Integer congue augue et malesuada iaculis</p><div class="buy"><strong>$&nbsp;2,100</strong><span class="btn">Add to Cart</span></div></article>
    <article class="product"><div class="photo g-silver" role="img" aria-label="Slim silver remote controls"></div><h4>Product Name</h4><p>Integer congue augue et malesuada iaculis</p><div class="buy"><strong>$&nbsp;2,100</strong><span class="btn">Add to Cart</span></div></article>
    <article class="product"><div class="photo g-screen" role="img" aria-label="All-in-one desktop computer set"></div><h4>Product Name</h4><p>Integer congue augue et malesuada iaculis</p><div class="buy"><strong>$&nbsp;2,100</strong><span class="btn">Add to Cart</span></div></article>
    <article class="product"><div class="photo g-dark" role="img" aria-label="Flat screen monitor"></div><h4>Product Name</h4><p>Integer congue augue et malesuada iaculis</p><div class="buy"><strong>$&nbsp;2,100</strong><span class="btn">Add to Cart</span></div></article>
  </div>

  <div class="section-head stores-head">Items from seller stores
    <div class="arrows"><svg viewBox="0 0 8 12"><path d="M7 1L2 6l5 5"/></svg><svg viewBox="0 0 8 12"><path d="M1 1l5 5-5 5"/></svg></div>
  </div>
  <div class="products" style="top:775px">
    <article class="product"><div class="photo g-dark" role="img" aria-label="Tablet computer"></div><h4>Product Name</h4><p>Integer congue augue et malesuada iaculis</p><div class="buy"><strong>$&nbsp;2,100</strong><span class="btn">Add to Cart</span></div></article>
    <article class="product"><div class="photo g-teal" role="img" aria-label="Turquoise compact camera"></div><h4>Product Name</h4><p>Integer congue augue et malesuada iaculis</p><div class="buy"><strong>$&nbsp;2,100</strong><span class="btn">Add to Cart</span></div></article>
    <article class="product"><div class="photo g-silver" role="img" aria-label="White portable hard drive"></div><h4>Product Name</h4><p>Integer congue augue et malesuada iaculis</p><div class="buy"><strong>$&nbsp;2,100</strong><span class="btn">Add to Cart</span></div></article>
    <article class="product"><div class="photo g-dark" role="img" aria-label="Black external hard drive"></div><h4>Product Name</h4><p>Integer congue augue et malesuada iaculis</p><div class="buy"><strong>$&nbsp;2,100</strong><span class="btn">Add to Cart</span></div></article>
    <article class="product"><div class="photo g-dark" role="img" aria-label="Black rangefinder camera"></div><h4>Product Name</h4><p>Integer congue augue et malesuada iaculis</p><div class="buy"><strong>$&nbsp;2,100</strong><span class="btn">Add to Cart</span></div></article>
  </div>

  <footer class="footer">
    <section><h5>Company</h5><ul><li>About Us</li><li>News</li><li>Feeds</li><li>Best Sellings</li><li>Products</li></ul></section>
    <section><h5>Sell &amp; Buy</h5><ul><li>Sell New Item</li><li>Sell Bulk Items</li><li>Categories</li><li>Currency Converter</li></ul></section>
    <section><h5>Others</h5><ul><li>Advertising</li><li>Knowledge Base</li><li>Forum</li><li>Stores</li></ul></section>
    <section><h5>Support</h5><ul><li>Contact</li><li>Terms of Use</li><li>Policy Privacy</li><li>RSS</li></ul></section>
    <section><h5>Stay in Touch</h5><div class="social"><span aria-label="Social link"></span><span aria-label="Social link"></span><span aria-label="Social link"></span><span aria-label="Social link"></span></div></section>
  </footer>
  <div class="bottombar">© 2014 Company Name  All right reserved  Term of Use</div>
</div>
</body>
</html>
```